Web design for Crowdfunding site HopeWingsRally.com

We need a web design for christian crowdfunding website. Here is the challenge: We need responsive layout that is targeted first in iPad size of screen. It should also scale somehow down to iPhone size of screens. Web layout can be about the same size as iPad screen.

Screens should work so that main page scrolls not but only certain part of the screen scrolls and always one "page" at time. We can implement these "scrolls" then later with javascript but now we need only design. The challenge is to create this kind of hybrid website / app look.

Target is at first to raise funds to orphan people needing about $40 per month for their living and education. There is always some organization which takes care of these kids. Later there will be other christian missions included. At first we are looking to find monthly supporters.

You can be as creative as you want :) As you see from the look and feel sector, I am not looking any same traditional look which many "help kids" sites have. I am looking to reach now younger generation and therefore iPad and mobile are the main screen sizes.

Inspirational designs:
- https://example-gallery.test/profiles/studiofernlake/designs/482716?from=%2Fbrowse%2Fxhr%2Fdesigns%3Fcategory%3Dmobile-app-design
- http://www.artpoolhub.test/design/8261047 Clear, simple visuals
- http://www.artpoolhub.test/design/7394215 Header
- http://www.artpoolhub.test/design/6048392 Contrast in the colors, i think is powerfull

Some terms could be: Kids play, kids are learning (in the school). No static posture but living like kids are. I wonder also how we could also add little bit gaming style even though the question is of reali life of real people. Giving should be rewarding.

Target Market(s)

People who want help other people.

Industry/Entity Type

Christian

Number of Pages Required

4 page

Requirements
Must have
• Homepage. Mission page (In my wireframes it was one kid).
Nice to have
• Other pages and some idea how to scroll. 4 pages is no must. If you feel easy, please give first some draft and I give comments on that.

```html
<!DOCTYPE html>
<html lang="en">
<head>
<meta charset="utf-8">
<title>HopeWingsRally – Mission page</title>
<link href="https://fonts.googleapis.com/css2?family=Roboto:wght@300;400;500;700&display=swap" rel="stylesheet">
<style>
:root{
  --yellow:#fbb400;
  --dark:#2c2c2c;
  --header:#2a2a2a;
  --panel:#eeeeee;
  --line:#cfcfcf;
  --text:#2b2b2b;
  --muted:#666;
  --blue:#2a9fd6;
  --blue-light:#d4ecf8;
  --white:#fff;
}
*{box-sizing:border-box;margin:0;padding:0}
html,body{width:1200px;height:1149px;overflow:hidden}
body{font-family:'Roboto',sans-serif;background:var(--white);color:var(--text);position:relative}

/* header */
.site-header{position:absolute;top:0;left:0;width:1200px;height:69px;background:var(--header)}
.menu-toggle{position:absolute;left:0;top:0;width:68px;height:69px;background:var(--yellow)}
.menu-toggle span{position:absolute;left:20px;width:26px;height:2px;background:var(--white)}
.nav-link{position:absolute;left:91px;top:28px;color:var(--white);font-size:12.5px;font-weight:400;letter-spacing:-.2px}
.search-icon{position:absolute;left:220px;top:28px}
.brand{position:absolute;left:0;width:1200px;top:18px;text-align:center;color:var(--yellow);font-size:27px;font-weight:700;letter-spacing:-.3px}
.social{position:absolute;top:20px;width:28px;height:28px;border-radius:50%;background:#555}
.btn{position:absolute;top:20px;width:84px;height:33px;background:var(--yellow);color:var(--white);font-size:12.5px;text-align:center;line-height:32px;border-bottom:3px solid #e09a00}

/* hero */
.hero{position:absolute;top:69px;left:0;width:1200px;height:363px;background:linear-gradient(180deg,#7f8a94 0%,#6c7986 40%,#3e5468 75%,#2e465c 100%)}
.hero-title{position:absolute;left:98px;top:236px;color:var(--white);font-size:43px;font-weight:300;letter-spacing:-.5px}
.tabs{position:absolute;left:99px;top:320px;display:flex;height:43px}
.tab{width:210px;background:var(--dark);color:var(--yellow);font-size:16px;padding-left:18px;line-height:43px;border-right:1px solid #444}
.tab.active{background:var(--yellow);color:var(--dark)}
.avatar{position:absolute;left:774px;top:216px;width:120px;height:120px;border-radius:50%;border:3px solid var(--yellow);background:radial-gradient(circle at 50% 45%,#c89478 0%,#8a4a36 55%,#5a2d22 100%)}
.profile{position:absolute;left:916px;top:240px;color:var(--white)}
.profile .name{font-size:15.5px;font-weight:300}
.profile .meta{font-size:12.5px;margin-top:10px;display:flex;align-items:center;gap:5px}
.profile .meta.org{margin-top:7px;padding-left:15px}

/* story */
.story{position:absolute;left:0;top:432px;width:772px;height:663px}
.timeline-line{position:absolute;left:113px;top:60px;width:1px;height:535px;background:var(--line)}
.dot{position:absolute;left:103px;width:22px;height:22px;border-radius:50%;background:var(--white);border:1px solid var(--line)}
.dot.active{background:var(--yellow);border-color:var(--yellow)}
.entry{position:absolute;left:152px;width:560px}
.entry h2{font-size:16.5px;font-weight:400;line-height:27.5px;color:var(--text)}
.entry p{font-size:12.5px;font-weight:300;line-height:23px;color:var(--muted);margin-top:6px}
.story-photo{position:absolute;left:152px;top:234px;width:574px;height:195px;background:linear-gradient(160deg,#b9c6cf 0%,#8c8a7a 40%,#7a5a36 70%,#3e3a22 100%)}

/* sidebar */
.sidebar{position:absolute;left:772px;top:432px;width:329px;height:663px;background:var(--panel)}
.side-title{position:absolute;left:30px;font-size:19.5px;font-weight:300;color:var(--text)}
.rule{position:absolute;left:30px;width:270px;height:2px;background:#aaa}
.supporter{position:absolute;top:27px;width:37px;height:37px;border-radius:50%;background:var(--yellow)}
.support-note{position:absolute;left:33px;top:100px;font-size:15px;font-weight:300}
.donut{position:absolute;left:34px;top:142px}
.given{position:absolute;left:165px;top:150px}
.given .amount{font-size:19.5px;font-weight:300}
.given .small{font-size:12.5px;color:var(--muted);font-weight:300;margin-top:12px}
.given .need{display:flex;align-items:center;gap:5px;margin-top:9px}
.option{position:absolute;left:30px;width:270px;height:45px;background:var(--white);border:1px solid #ddd;display:flex;align-items:center;padding-left:15px;font-size:14.5px;font-weight:300}
.check{width:19px;height:19px;border:1px solid #ccc;border-radius:3px;background:#f7f7f7;margin-right:12px}
.cart{position:absolute;right:10px;top:11px}
.amount-input{position:absolute;left:134px;top:9px;width:92px;height:27px;border:1px solid #ccc;font-size:11px;color:#999;padding-left:10px;line-height:25px}

/* footer */
.site-footer{position:absolute;top:1095px;left:0;width:1200px;height:54px;background:var(--dark);color:#ccc;font-size:12.5px;font-weight:300;text-align:center;line-height:54px}
</style>
</head>
<body>

<header class="site-header">
  <div class="menu-toggle"><span style="top:24px"></span><span style="top:33px"></span><span style="top:42px"></span></div>
  <div class="nav-link">SEE THE MISSIONS</div>
  <svg class="search-icon" width="14" height="14" viewBox="0 0 14 14"><circle cx="5.5" cy="5.5" r="4.2" fill="none" stroke="#fff" stroke-width="1.8"/><line x1="8.6" y1="8.6" x2="12.5" y2="12.5" stroke="#fff" stroke-width="2"/></svg>
  <div class="brand">HOPEWINGSRALLY</div>
  <div class="social" style="left:862px"></div>
  <div class="social" style="left:897px"></div>
  <div class="social" style="left:931px"></div>
  <div class="btn" style="left:983px">LOGIN</div>
  <div class="btn" style="left:1077px">SIGNUP</div>
</header>

<section class="hero" role="img" aria-label="Misty mountain peak with a statue on its summit under a cloudy sky">
  <h1 class="hero-title">Mission: Orphan Lena, Ody</h1>
  <nav class="tabs">
    <div class="tab active">STORY</div>
    <div class="tab">UPDATES</div>
    <div class="tab">COMMENTS</div>
  </nav>
  <div class="avatar" role="img" aria-label="Portrait photo of the child"></div>
  <div class="profile">
    <div class="name">Name: Lena, Ody</div>
    <div class="meta"><svg width="10" height="13" viewBox="0 0 10 13"><path d="M5 0C2.2 0 0 2.2 0 5c0 3.5 5 8 5 8s5-4.5 5-8c0-2.8-2.2-5-5-5zm0 7a2 2 0 1 1 0-4 2 2 0 0 1 0 4z" fill="#fbb400"/></svg>Kalkutta</div>
    <div class="meta org">Organization : Ardent</div>
  </div>
</section>

<main class="story">
  <div class="timeline-line"></div>
  <div class="dot" style="top:50px"></div>
  <div class="dot active" style="top:322px"></div>
  <div class="dot" style="top:585px"></div>

  <article class="entry" style="top:45px">
    <h2>Lorem Ipsum is simply dummy text of the printing and typesetting industry. Lorem Ipsum has been the industry’s standard</h2>
    <p>Lorem Ipsum is simply dummy text of the printing and typesetting industry. Lorem Ipsum has been the industry’s standard dummy text ever since the 1500s, when an unknown printer took a galley of type and scrambled it to make a type specimen book. It has survived not only five centuries, but also the leap into electronic typesetting, remaining essentially unchanged.</p>
  </article>

  <div class="story-photo" role="img" aria-label="Hiker with backpack walking a mountain ridge at sunset"></div>

  <article class="entry" style="top:455px">
    <h2>Lorem Ipsum is simply dummy text of the printing and typesetting industry. Lorem Ipsum has been the industry’s standard</h2>
    <p>Lorem Ipsum is simply dummy text of the printing and typesetting industry. Lorem Ipsum has been the industry’s standard dummy text ever since the 1500s, when an unknown printer took a galley of type and scrambled it to make a type specimen book. It has survived not only five centuries, but also the leap into electronic typesetting, remaining essentially unchanged.</p>
  </article>
</main>

<aside class="sidebar">
  <div class="side-title" style="top:34px">Support</div>
  <div class="supporter" style="left:114px"></div>
  <div class="supporter" style="left:157px"></div>
  <div class="supporter" style="left:200px"></div>
  <div class="supporter" style="left:243px"></div>
  <svg style="position:absolute;left:290px;top:32px" width="10" height="28" viewBox="0 0 10 28"><polyline points="1,1 9,14 1,27" fill="none" stroke="#555" stroke-width="1.3"/></svg>
  <div class="rule" style="top:80px"></div>
  <div class="support-note">My support is now : $15 given</div>

  <svg class="donut" width="110" height="110" viewBox="0 0 110 110">
    <circle cx="55" cy="55" r="49" fill="none" stroke="var(--blue-light)" stroke-width="8"/>
    <circle cx="55" cy="55" r="49" fill="none" stroke="var(--blue)" stroke-width="8" stroke-dasharray="184.7 307.9" transform="rotate(-90 55 55) scale(1 -1) translate(0 -110)"/>
    <text x="55" y="66" text-anchor="middle" font-family="Roboto, sans-serif" font-size="31" font-weight="300" fill="var(--blue)">60%</text>
  </svg>
  <div class="given">
    <div class="amount">$15 given</div>
    <div class="small">of total $35 needed</div>
    <div class="small need"><svg width="13" height="13" viewBox="0 0 13 13"><rect x="0.5" y="2" width="12" height="10.5" fill="none" stroke="#fbb400"/><rect x="0.5" y="2" width="12" height="3" fill="#fbb400"/><rect x="3" y="0" width="1.5" height="3" fill="#fbb400"/><rect x="8.5" y="0" width="1.5" height="3" fill="#fbb400"/></svg>Per month need</div>
  </div>

  <div class="side-title" style="top:280px">Participate</div>
  <div class="rule" style="top:318px"></div>

  <div class="option" style="top:339px"><span class="check"></span>I am in, $1 / Month<svg class="cart" width="25" height="24" viewBox="0 0 25 24"><g fill="none" stroke="#666" stroke-width="1.3"><path d="M1 2h3l3 14h14l3-10H6"/><line x1="11" y1="9" x2="11" y2="13"/><line x1="14" y1="9" x2="14" y2="13"/><line x1="17" y1="9" x2="17" y2="13"/><circle cx="9" cy="20" r="1.8"/><circle cx="19" cy="20" r="1.8"/></g></svg></div>
  <div class="option" style="top:392px"><span class="check"></span>Increased, $5 / Month<svg class="cart" width="25" height="24" viewBox="0 0 25 24"><g fill="none" stroke="#666" stroke-width="1.3"><path d="M1 2h3l3 14h14l3-10H6"/><line x1="11" y1="9" x2="11" y2="13"/><line x1="14" y1="9" x2="14" y2="13"/><line x1="17" y1="9" x2="17" y2="13"/><circle cx="9" cy="20" r="1.8"/><circle cx="19" cy="20" r="1.8"/></g></svg></div>
  <div class="option" style="top:445px"><span class="check"></span>Decent help, $10 / Month<svg class="cart" width="25" height="24" viewBox="0 0 25 24"><g fill="none" stroke="#666" stroke-width="1.3"><path d="M1 2h3l3 14h14l3-10H6"/><line x1="11" y1="9" x2="11" y2="13"/><line x1="14" y1="9" x2="14" y2="13"/><line x1="17" y1="9" x2="17" y2="13"/><circle cx="9" cy="20" r="1.8"/><circle cx="19" cy="20" r="1.8"/></g></svg></div>
  <div class="option" style="top:498px"><span class="check"></span>Whole Kid, $35 / Month<svg class="cart" width="25" height="24" viewBox="0 0 25 24"><g fill="none" stroke="#666" stroke-width="1.3"><path d="M1 2h3l3 14h14l3-10H6"/><line x1="11" y1="9" x2="11" y2="13"/><line x1="14" y1="9" x2="14" y2="13"/><line x1="17" y1="9" x2="17" y2="13"/><circle cx="9" cy="20" r="1.8"/><circle cx="19" cy="20" r="1.8"/></g></svg></div>
  <div class="option" style="top:551px"><span class="check"></span>My Amount<span class="amount-input">Enter Amount</span><svg class="cart" width="25" height="24" viewBox="0 0 25 24"><g fill="none" stroke="#666" stroke-width="1.3"><path d="M1 2h3l3 14h14l3-10H6"/><line x1="11" y1="9" x2="11" y2="13"/><line x1="14" y1="9" x2="14" y2="13"/><line x1="17" y1="9" x2="17" y2="13"/><circle cx="9" cy="20" r="1.8"/><circle cx="19" cy="20" r="1.8"/></g></svg></div>
</aside>

<footer class="site-footer">Copyrights. 2016. HopeWingsRally. All rights reserved.</footer>

</body>
</html>
```